Travel Agency Website - Simple General

Need a 7 page simple design that is pretty repetitive. Need to be able to load quickly that is SEO optimized. Trying to give ideas on what they can do, be personal as we are local, but at the same time come across as professional and get information easily with little burden.

- Landing Page
- Brimwell Vacations Page
- Family Trips
- Road Trips from Texas
- Other Destinations
- About Us Page
- Contact Us Page

Target Market(s)

Families

Coding

Coded - Design and coding required

Number of Pages Required

5+ page

Colors

Designer to choose colors to be used in the design.

Requirements
Must have
• Like it to flow easily with our logo. Use that for colors, etc.

```html
<!DOCTYPE html>
<html lang="en">
<head>
<meta charset="utf-8">
<title>Wayfarer Lane Travel Co. — Explore Beyond the Ordinary</title>
<link rel="stylesheet" href="https://fonts.googleapis.com/css2?family=Outfit:wght@400;500;600;700&display=swap">
<style>
:root{
  --gold:#c49a52;
  --gold-deep:#b58a40;
  --teal:#26807f;
  --white:#ffffff;
  --line:rgba(255,255,255,.45);
}
*{margin:0;padding:0;box-sizing:border-box}
html,body{width:1200px;height:847px;overflow:hidden}
body{font-family:"Outfit",sans-serif;color:var(--white);position:relative;background:#6a3a1e}
.hero-photo{position:absolute;left:0;top:0;width:1200px;height:788px;
  background:
    radial-gradient(ellipse 380px 260px at 1120px 420px, rgba(255,214,140,.95), rgba(255,180,90,0) 70%),
    radial-gradient(ellipse 420px 170px at 860px 360px, rgba(236,222,200,.95), rgba(236,222,200,0) 75%),
    radial-gradient(ellipse 520px 420px at 80px 120px, rgba(120,150,175,.95), rgba(120,150,175,0) 70%),
    linear-gradient(180deg,#8a4a22 0%,#a85a26 30%,#c98a52 55%,#c7824a 72%,#8e5230 100%);}
.hero-shade{position:absolute;inset:0;height:788px;background:linear-gradient(90deg,rgba(40,20,10,.35),rgba(40,20,10,0) 60%)}
.brand{position:absolute;left:85px;top:62px;display:flex;align-items:center;gap:10px;font-weight:600;font-size:24px;line-height:1.1}
.brand-dot{width:18px;height:18px;border-radius:50%;background:var(--gold)}
.topbar{position:absolute;left:262px;right:76px;top:0;height:66px;border-bottom:1px solid var(--line);display:flex;justify-content:flex-end;align-items:center;gap:34px;padding-right:10px}
.contact-item{display:flex;align-items:center;gap:8px;font-size:14px;font-weight:500}
.contact-icon{width:28px;height:28px;border-radius:50%;background:var(--white);display:flex;align-items:center;justify-content:center}
.main-nav{position:absolute;left:262px;right:76px;top:66px;height:59px;border-bottom:1px solid var(--line);display:flex;align-items:center;font-size:15.5px;font-weight:500}
.main-nav a{color:var(--white);text-decoration:none;position:absolute;top:50%;transform:translateY(-50%)}
.btn-contact{left:719px;width:143px;height:38px;border-radius:19px;background:var(--gold);display:flex;align-items:center;justify-content:space-between;padding:0 7px 0 29px;font-size:14px}
.btn-contact span{width:27px;height:27px;border-radius:50%;background:var(--gold-deep);display:flex;align-items:center;justify-content:center}
.slider-dots{position:absolute;left:26px;top:312px;display:flex;flex-direction:column;align-items:center;gap:15px}
.slider-dots i{display:block;width:8px;height:8px;border-radius:50%;background:var(--white)}
.slider-dots i.active{width:20px;height:20px;border:2px solid var(--white);background:transparent;position:relative}
.slider-dots i.active::after{content:"";position:absolute;left:4px;top:4px;width:8px;height:8px;border-radius:50%;background:var(--white)}
.hero-copy{position:absolute;left:114px;top:277px}
.hero-title{font-size:57px;font-weight:600;line-height:54px;letter-spacing:.5px;text-transform:uppercase}
.hero-text{margin-top:21px;font-size:23px;line-height:27px;font-weight:400;width:360px}
.btn-discover{margin-top:30px;display:inline-flex;align-items:center;gap:10px;height:51px;width:289px;justify-content:center;background:var(--gold);color:var(--white);text-decoration:none;font-size:17px;font-weight:600;text-transform:uppercase;letter-spacing:.3px}
.site-footer{position:absolute;left:0;bottom:0;width:1200px;height:59px;background:var(--teal);display:flex;align-items:center;justify-content:center;font-size:13.5px}
.social{position:absolute;right:103px;top:18px;display:flex;gap:8px}
.social span{width:23px;height:23px;border-radius:50%;background:var(--white)}
</style>
</head>
<body>
<div class="hero-photo" role="img" aria-label="Two hikers walking under a sunlit red sandstone arch in a rocky desert landscape"></div>
<div class="hero-shade"></div>

<div class="brand"><span class="brand-dot"></span><span>Wayfarer Lane<br>Travel Co.</span></div>

<div class="topbar">
  <div class="contact-item"><span class="contact-icon"><svg width="16" height="12" viewBox="0 0 16 12"><rect x="1" y="1" width="14" height="10" rx="1" fill="none" stroke="#333" stroke-width="1.4"/><path d="M1 1l7 6 7-6" fill="none" stroke="#333" stroke-width="1.4"/></svg></span>hello@wayfarerlanetravel.com</div>
  <div class="contact-item"><span class="contact-icon"><svg width="14" height="14" viewBox="0 0 24 24"><path fill="#333" d="M6.6 10.8a15.1 15.1 0 0 0 6.6 6.6l2.2-2.2c.3-.3.7-.4 1-.2 1.1.4 2.3.6 3.6.6.6 0 1 .4 1 1V20c0 .6-.4 1-1 1A17 17 0 0 1 3 4c0-.6.4-1 1-1h3.5c.6 0 1 .4 1 1 0 1.3.2 2.5.6 3.6.1.3 0 .7-.2 1z"/></svg></span>Phone Number (123) 456 7890</div>
</div>

<nav class="main-nav">
  <a href="#" style="left:30px" aria-label="Home"><svg width="14" height="13" viewBox="0 0 14 13"><path d="M7 0L0 6h2v7h4V9h2v4h4V6h2z" fill="#fff"/></svg></a>
  <a href="#" style="left:70px">Brimwell Vacations</a>
  <a href="#" style="left:215px">Family Trips</a>
  <a href="#" style="left:321px">Texas Road Trips</a>
  <a href="#" style="left:467px">Other Destinations</a>
  <a href="#" style="left:636px">About Us</a>
  <a href="#" class="btn-contact">Contact Us <span><svg width="10" height="10" viewBox="0 0 10 10"><path d="M2 8L8 2M3 2h5v5" fill="none" stroke="#fff" stroke-width="1.5"/></svg></span></a>
</nav>

<div class="slider-dots"><i></i><i></i><i></i><i class="active"></i></div>

<section class="hero-copy">
  <h1 class="hero-title">Explore Beyond<br>the Ordinary</h1>
  <p class="hero-text">From hidden gems to bucket-list destinations, we help you travel anywhere your heart desires.</p>
  <a href="#" class="btn-discover">Discover Destinations <svg width="11" height="11" viewBox="0 0 10 10"><path d="M2 8L8 2M3 2h5v5" fill="none" stroke="#fff" stroke-width="1.6"/></svg></a>
</section>

<footer class="site-footer">
  <p>© 2026 Wayfarer Lane Travel Co. All Right Reserved</p>
  <div class="social"><span></span><span></span></div>
</footer>
</body>
</html>
```